BOLD & MINIMALIST DESIGN NEEDED

We want a very bold but minimalistic business card design that is impactful and utilizes both sides of the business card. Our current logo is included for your use.

We want bold fonts and good use of negative space. We don't want the logo to overpower the design.

Target Market(s)

Professionals who are building new commercial buildings.

Industry/Entity Type

Construction

Contact Information for Business Card

Name, Title, email, office phone, cell phone, website

Font styles to use
Serif
Sans Serif

Requirements
Must have
• Bold design!

```html
<!DOCTYPE html>
<html lang="en">
<head>
<meta charset="utf-8">
<title>Ridgeline Design + Build — Business Card</title>
<link href="https://fonts.googleapis.com/css2?family=Montserrat:wght@400;600;800&display=swap" rel="stylesheet">
<style>
  :root {
    --backdrop: #3a3a3a;
    --card: #1d1d1d;
    --card-deep: #141414;
    --accent: #8cc63f;
    --text-light: #e8e8e8;
    --text-muted: #cfcfcf;
  }
  * { margin: 0; padding: 0; box-sizing: border-box; }
  html, body {
    width: 1200px; height: 791px; overflow: hidden;
    background: var(--backdrop);
    font-family: "Montserrat", sans-serif;
  }
  .stage {
    position: relative; width: 1200px; height: 791px;
    display: flex; align-items: center; justify-content: center; gap: 60px;
  }
  .card {
    position: relative; width: 520px; height: 297px;
    background: var(--card);
    border: 2px solid var(--accent);
    box-shadow: 0 18px 40px rgba(0,0,0,0.45);
    overflow: hidden;
  }
  /* Front */
  .card-front { display: flex; }
  .brand-block {
    width: 52%; display: flex; flex-direction: column;
    align-items: center; justify-content: center; gap: 10px;
    padding-top: 60px;
  }
  .brand-mark { display: flex; align-items: center; gap: 10px; }
  .brand-dot { width: 14px; height: 14px; background: var(--accent); }
  .brand-name {
    font-weight: 800; font-size: 30px; letter-spacing: 1px;
    color: var(--text-light); text-transform: uppercase;
  }
  .brand-tagline {
    font-weight: 400; font-size: 11px; letter-spacing: 5px;
    color: var(--text-light); text-transform: uppercase;
  }
  .divider {
    width: 1px; background: var(--accent);
    margin: 48px 0 98px;
  }
  .contact-block {
    flex: 1; padding: 34px 0 0 30px;
    display: flex; flex-direction: column;
  }
  .person-name {
    font-weight: 800; font-size: 19px; color: var(--accent);
    text-transform: uppercase; letter-spacing: 0.5px;
  }
  .person-title {
    font-weight: 400; font-size: 13px; color: var(--text-light);
    margin-top: 2px;
  }
  .contact-list { list-style: none; margin-top: 34px; }
  .contact-list li {
    display: flex; align-items: center; gap: 9px;
    font-size: 12.5px; color: var(--text-muted);
    margin-bottom: 6px; letter-spacing: 0.3px;
  }
  .contact-list svg { width: 11px; height: 11px; flex: none; }
  /* Back */
  .card-back { background: var(--card-deep); }
  .pattern-field {
    position: absolute; inset: 0;
    background: linear-gradient(120deg, #0c0c0c 0%, #1a1a1a 45%, #3a3a3a 100%);
  }
  .back-center {
    position: absolute; inset: 0;
    display: flex; align-items: center; justify-content: center; gap: 10px;
  }
  .back-center .brand-name { font-size: 26px; }
</style>
</head>
<body>
<main class="stage">
  <section class="card card-front" aria-label="Card front">
    <div class="brand-block">
      <div class="brand-mark">
        <span class="brand-dot"></span>
        <span class="brand-name">Ridgeline</span>
      </div>
      <span class="brand-tagline">Design + Build</span>
    </div>
    <div class="divider"></div>
    <div class="contact-block">
      <h1 class="person-name">Marcus Delane</h1>
      <p class="person-title">President</p>
      <ul class="contact-list">
        <li>
          <svg viewBox="0 0 12 12"><path d="M2.5 1 L4.5 1 L5 3.5 L3.8 4.5 Q5 7 7.5 8.2 L8.5 7 L11 7.5 L11 9.5 Q10 11 8 11 Q1 9 1 3 Q1 1 2.5 1Z" fill="var(--accent)"/></svg>
          555-014-2200
        </li>
        <li>
          <svg viewBox="0 0 12 12"><rect x="3" y="0.8" width="6" height="10.4" rx="1" fill="none" stroke="var(--text-muted)" stroke-width="1.2"/><circle cx="6" cy="9.4" r="0.6" fill="var(--text-muted)"/></svg>
          555-014-2200
        </li>
        <li>
          <svg viewBox="0 0 12 12"><rect x="1" y="2.5" width="10" height="7" fill="var(--accent)"/><path d="M1 2.5 L6 6.5 L11 2.5" fill="none" stroke="var(--card)" stroke-width="1"/></svg>
          m.delane@ridgeline-db.com
        </li>
        <li>
          <svg viewBox="0 0 12 12"><circle cx="6" cy="6" r="5" fill="var(--accent)"/><path d="M1 6 H11 M6 1 Q3 6 6 11 M6 1 Q9 6 6 11" fill="none" stroke="var(--card)" stroke-width="0.8"/></svg>
          www.ridgeline-db.com
        </li>
      </ul>
    </div>
  </section>

  <section class="card card-back" aria-label="Card back">
    <div class="pattern-field" role="img" aria-label="Repeating tonal brand pattern in glossy black and dark grey"></div>
    <div class="back-center">
      <span class="brand-dot"></span>
      <span class="brand-name">Ridgeline</span>
    </div>
  </section>
</main>
</body>
</html>
```